new letterhead for my brokergae company KeelBright, Complete Marine Brokering

We need a new letterhead for our brokerage company called KeelBright. We are specialised in selling pleasure crafts (sailing and motoryachts). More info can be found at https://keelbright-example.com/en

I use this document for a quotation, a letter, sales agreement, selling instructions. I am looking for a cover page + a content page.

Th efollowing information needs to be in the header / footer; email, website, VAT number, Bank Account number, number chamber of ccomerce, registry number olpa, General terms and conditions TQRV apply.

```html
<!DOCTYPE html>
<html lang="en">
<head>
<meta charset="utf-8">
<title>KeelBright – Cover and Letterhead</title>
<link rel="stylesheet" href="https://fonts.googleapis.com/css2?family=Raleway:wght@300;400;600&family=Arimo:wght@400&display=swap">
<style>
  :root{
    --backdrop:#e2e2e4;
    --brand-blue:#0f5aa3;
    --brand-blue-deep:#0b4f8c;
    --sky-blue:#5aaedb;
    --stone:#8a8a8c;
    --stone-light:#b9b9c0;
    --paper:#f5f5f5;
    --ink:#2b2b2b;
    --white:#ffffff;
  }
  *{margin:0;padding:0;box-sizing:border-box}
  html,body{width:1200px;height:901px;overflow:hidden;background:var(--backdrop)}
  .canvas{position:relative;width:1200px;height:901px}
  .page{position:absolute;top:105px;width:490px;height:692px;overflow:hidden}

  /* Cover page */
  .cover{left:82px;background:var(--brand-blue)}
  .cover-column{position:absolute;left:358px;top:0;width:93px;height:302px;background:var(--brand-blue-deep)}
  .cover-brand{position:absolute;left:50px;top:70px;color:var(--white);font-family:"Raleway",sans-serif}
  .cover-brand .name{font-weight:400;font-size:30px;letter-spacing:.5px;display:flex;align-items:center;gap:10px}
  .cover-brand .mark{width:12px;height:12px;border-radius:50%;background:var(--white)}
  .cover-brand .tagline{font-size:7px;font-weight:400;letter-spacing:2.2px;text-transform:uppercase;margin-top:6px;margin-left:22px}
  .cover-title{position:absolute;left:47px;top:212px;font-family:"Raleway",sans-serif;font-weight:300;line-height:1}
  .cover-title .small{color:var(--white);font-size:27px;letter-spacing:.5px}
  .cover-title .large{color:var(--stone-light);font-size:52px;letter-spacing:1px;margin-top:6px}
  .cover-photo{position:absolute;left:0;top:302px;width:490px;height:221px;
    background:linear-gradient(180deg,#3a4048 0%,#5f6a78 30%,#24558a 62%,#123f74 100%)}
  .cover-photo-tint{position:absolute;left:358px;top:302px;width:93px;height:221px;background:var(--sky-blue);opacity:.72}
  .cover-base{position:absolute;left:0;top:523px;width:490px;height:169px;background:var(--stone)}
  .cover-base-column{position:absolute;left:358px;top:523px;width:93px;height:169px;background:var(--brand-blue)}
  .confidential{position:absolute;left:49px;top:645px;width:238px;border-top:1px solid #a2a2a4;padding-top:4px;
    font-family:"Arimo",sans-serif;font-size:4.6px;line-height:5.6px;color:#a9a9ab}
  .confidential strong{font-weight:400;display:block}

  /* Letter page */
  .letter{left:630px;background:var(--paper);font-family:"Arimo",sans-serif;color:var(--ink)}
  .letter-brand{position:absolute;left:39px;top:55px;color:var(--brand-blue);font-family:"Raleway",sans-serif}
  .letter-brand .name{font-size:21px;font-weight:400;display:flex;align-items:center;gap:7px}
  .letter-brand .mark{width:9px;height:9px;border-radius:50%;background:var(--brand-blue)}
  .letter-brand .tagline{font-size:5px;letter-spacing:1.4px;text-transform:uppercase;margin-top:3px;margin-left:16px}
  .company-details{position:absolute;right:38px;top:58px;text-align:right;font-size:6.2px;line-height:8.3px}
  .letter-date{position:absolute;left:39px;top:183px;font-size:7px}
  .recipient{position:absolute;left:39px;top:201px;font-size:7px;line-height:8.5px}
  .letter-body{position:absolute;left:39px;top:285px;width:413px;font-size:6.9px;line-height:8.6px;text-align:justify}
  .letter-body p{margin-bottom:8.6px}
  .closing{position:absolute;left:39px;top:477px;font-size:7px;line-height:8.5px}
  .signature{position:absolute;left:99px;top:470px;width:72px;height:34px;background:linear-gradient(90deg,rgba(70,80,170,.10),rgba(70,80,170,.18))}
  .letter-footer{position:absolute;left:0;top:671px;width:490px;height:21px}
  .web{position:absolute;right:38px;top:674px;font-size:6.5px;letter-spacing:1.4px;color:var(--ink)}
  .web b{color:var(--brand-blue);font-weight:400}
</style>
</head>
<body>
<div class="canvas">

  <section class="page cover">
    <div class="cover-column"></div>
    <div class="cover-brand">
      <div class="name"><span class="mark"></span>KeelBright</div>
      <div class="tagline">Complete Marine Brokering</div>
    </div>
    <h1 class="cover-title">
      <div class="small">BUSINESS</div>
      <div class="large">PROPOSAL</div>
    </h1>
    <div class="cover-photo" role="img" aria-label="Photograph of a dark-hulled sailing yacht under way on deep blue sea"></div>
    <div class="cover-photo-tint"></div>
    <div class="cover-base"></div>
    <div class="cover-base-column"></div>
    <div class="confidential">
      <strong>Statement of Confidentiality</strong>
      This proposal and supporting materials contain confidential and proprietary business information of KeelBright. These materials may be printed or photocopied for use in evaluating the proposed project, but are not to be shared with other parties.
    </div>
  </section>

  <section class="page letter">
    <div class="letter-brand">
      <div class="name"><span class="mark"></span>KeelBright</div>
      <div class="tagline">Complete Marine Brokering</div>
    </div>
    <div class="company-details">
      VAT: 1234567<br>
      Bank Account number: 1234567<br>
      Registry number olpa: 1234567
    </div>
    <div class="letter-date">30.09.2017</div>
    <address class="recipient" style="font-style:normal">
      Recipient's name<br>Hafenweg 4<br>20457 Hamburg<br>Germany
    </address>
    <div class="letter-body">
      <p style="margin-bottom:12px">Dear sir,</p>
      <p>Communication is a very integral part of living creatures, animals and humans. Communication may be verbal or written. Written communication however is only applicable to human beings. Can you even imagine a world without communication? Verbal communication can be through telephones, webcams or in person. Written communication is through letters, emails and mobile phone messages.</p>
      <p>In today's world of great inventions and technology, letters have somehow become redundant. It is the time for text messages or chats. But they still can communicate a lot more than all other modes of communication. Organizations and various government departments still bank on letters as a strong medium of communication. There is no comparison in costs of sending letters as compared to costs of mobile phone messages though – letters are far cheaper. Letters now commonly known as "hard copy documents" are considered more relevant and important than email copies of text messages as proof or evidence of some sort.</p>
      <p>Letters speak volumes about a person or an organization that writes it. So one must take utmost care ensuring that the language used in any letter is appropriate for the occasion for which it is being written. Since a letter is also a written proof or document, if there are certain things that should not form a part of it, then that too should be carefully handled.</p>
      <p>Writing a good letter is an art. But if for some reason someone is unable to write that perfect letter, these different types of letters provide a base for you to build on. Sample letters have been given for everyone to understand what all information needs to form a part of the letter type and then it can be customized.</p>
    </div>
    <div class="closing">Yours Sincerely,<br>Lorin Vask</div>
    <div class="signature" role="img" aria-label="Handwritten signature"></div>
    <svg class="letter-footer" viewBox="0 0 490 21" aria-hidden="true">
      <polygon points="0,0 310,0 292,21 0,21" fill="var(--brand-blue)"/>
      <polygon points="214,13 310,13 302,21 206,21" fill="var(--brand-blue-deep)"/>
      <polygon points="316,4 328,4 312,21 300,21" fill="#c8c8ca"/>
      <polygon points="322,13 490,13 490,21 314,21" fill="var(--stone)"/>
    </svg>
    <div class="web">www.<b>keelbright-example</b>.com</div>
  </section>

</div>
</body>
</html>
```